High-End Print/Digital Ad for Unique Luxury Travel Company Required

Objective:
Design a compelling and visually striking advertisement that highlights our company’s unmatched luxury travel experiences. The ad should elevate our brand image, spark curiosity, and drive prospective clients to contact us.
Target Audience:
• Affluent individuals seeking extraordinary, tailor-made travel experiences
• Affluent, luxury, high-net-worth individuals looking for value, expertise, and white-glove service
• Professionals or retirees who appreciate unique, thoughtfully curated travel over mainstream tourism
Key Messages to Communicate:
• One-of-a-kind luxury travel: Once-in-a-lifetime experiences that are curated with creativity and meticulous attention to detail
• Exceptional service: White-glove, personalized planning from start to finish
• 38 years’ travel experience – expert knowledge of destinations, modes of travel, premium accommodations and well-established, meaningful industry connections.
• Highly trusted: Cruise line executives often say, “No one does what you do.”
Tone and Style:
• Elegant, luxurious, sophisticated
• Eye-catching, polished, and modern
• Professional but warm—conveys trust and credibility
• High-impact visuals (full-bleed imagery, custom graphics, or high-end photography)
Deliverables:
• One full-page print ad and digital ad
• Ready-to-print, high-resolution file + working file (PSD, AI, etc.)
Optional: Social media-optimized version or short motion-graphic variation (if designer offers it)
Inspiration & Visual Style Suggestions:
• Think Lumen Voyages, Harrow Pike Wanderer, Silver Quill, or Orvel Retreats ad styles
• Large, emotive imagery with elegant typography
• Clean layout that speaks luxury, clarity, and trust
Copy Direction (draft):
For those who’ve explored the world—and crave something beyond the ordinary.
Each journey is a masterfully curated experience, rich in detail, seamless in execution, and unforgettable in every way.
Founded in 1997, Tidewell Journeys is a unique travel company specializing in cruising, all-inclusive luxury properties, and tours world-wide for individuals, groups, and incentives.
We offer an exceptional range of services designed to ensure every journey is flawlessly executed and truly unforgettable.
Let us help you plan your next extraordinary adventure.
Note: You may refine the copy slightly based on layout or format needs.
Other Resources for References:
1. Website - www.tidewelljourneys-example.com

```html
<!DOCTYPE html>
<html lang="en">
<head>
<meta charset="utf-8">
<title>Tidewell Journeys — Luxury Travel Ad Variations</title>
<link rel="stylesheet" href="https://fonts.googleapis.com/css2?family=EB+Garamond:ital,wght@0,400;0,600;1,400&family=Marcellus&display=swap">
<style>
  :root {
    --board: #999999;
    --paper: #ffffff;
    --ink: #2a2a2a;
    --brand-blue: #2b3f8f;
    --dot: #9a9aa0;
    --ice-deep: #0d4a66;
    --ice-mid: #1f86a8;
    --ice-light: #bfe9f3;
  }
  * { box-sizing: border-box; margin: 0; padding: 0; }
  html, body { width: 1200px; height: 842px; overflow: hidden; background: var(--board); }
  body { position: relative; font-family: "EB Garamond", Georgia, serif; color: var(--ink); }

  .ad-page {
    position: absolute; top: 42px; width: 534px; height: 756px;
    background: var(--paper); overflow: hidden;
  }
  .ad-page--framed { left: 48px; }
  .ad-page--bleed { left: 618px; }

  .hero-photo {
    position: absolute;
    background:
      radial-gradient(ellipse 32% 30% at 74% 62%, #ffffff 0%, var(--ice-light) 40%, rgba(191,233,243,0) 75%),
      radial-gradient(ellipse 60% 28% at 40% 95%, #0a1f2a 0%, rgba(10,31,42,0) 80%),
      linear-gradient(160deg, var(--ice-deep) 0%, var(--ice-mid) 45%, #3fa6c4 70%, #0f5875 100%);
  }
  .ad-page--framed .hero-photo { left: 14px; top: 13px; width: 506px; height: 398px; }
  .ad-page--bleed .hero-photo { left: 0; top: 0; width: 534px; height: 411px; }

  .display { font-family: "Marcellus", "Times New Roman", serif; color: #fff; font-weight: 400; white-space: nowrap; }
  .headline-stack { position: absolute; left: 37px; top: 60px; font-size: 45px; line-height: 60px; letter-spacing: -1.5px; }
  .headline-centered { position: absolute; left: 0; right: 0; text-align: center; }
  .headline-centered .kicker { position: absolute; left: 0; right: 0; top: 41px; font-size: 17px; letter-spacing: -0.3px; }
  .headline-centered .main { position: absolute; left: 0; right: 0; top: 65px; font-size: 25px; letter-spacing: -0.6px; }
  .headline-centered .tail { position: absolute; left: 0; right: 0; top: 102px; font-size: 17px; letter-spacing: -0.3px; }

  .invite { position: absolute; left: 0; right: 0; top: 420px; text-align: center; font-size: 8.6px; }
  .rule-h { position: absolute; height: 0; border-top: 1.6px dotted var(--dot); }
  .rule-v { position: absolute; width: 0; border-left: 1.6px dotted var(--dot); }
  .rule-invite { left: 132px; width: 272px; top: 444px; }

  .intro-copy { position: absolute; left: 48px; top: 462px; width: 136px; font-size: 7.9px; line-height: 10.8px; }
  .intro-copy p + p { margin-top: 10.5px; }
  .rule-left { left: 195px; top: 465px; height: 168px; }
  .rule-right { left: 341px; top: 465px; height: 168px; }

  .gallery-photo { position: absolute; left: 208px; width: 122px; }
  .gallery-photo--ship { top: 465px; height: 88px; background: linear-gradient(180deg, #7d86b8 0%, #c9cde3 45%, #e9e4de 62%, #5f7f9e 78%, #2f4f72 100%); }
  .gallery-photo--park { top: 563px; height: 68px; background: linear-gradient(180deg, #e9b779 0%, #d8a26a 30%, #6f8a4a 60%, #b96b3c 85%, #d9c15a 100%); }

  .benefits { position: absolute; left: 354px; top: 461px; width: 128px; font-size: 7.9px; line-height: 9.7px; }
  .benefit + .benefit { margin-top: 9px; }
  .benefit h3 { font-family: "Marcellus", "Times New Roman", serif; font-weight: 400; color: var(--brand-blue); font-size: 8.4px; line-height: 10px; letter-spacing: -0.2px; white-space: nowrap; }
  .benefit em { font-style: italic; }

  .brand-mark { position: absolute; left: 0; right: 0; display: flex; justify-content: center; align-items: center; gap: 5px; }
  .brand-mark .brand-dot { width: 13px; height: 13px; border-radius: 50%; background: var(--brand-blue); }
  .brand-mark .brand-name { font-family: "Marcellus", "Times New Roman", serif; color: var(--brand-blue); font-size: 17px; letter-spacing: 0.2px; }

  .ad-page--framed .brand-mark { top: 672px; left: 90px; right: auto; width: 370px; }
  .closing-bold { position: absolute; left: 90px; width: 370px; top: 704px; text-align: center; font-weight: 600; font-size: 8.6px; line-height: 11px; }

  .contact-list { position: absolute; font-size: 8.4px; line-height: 15px; list-style: none; }
  .contact-list li { display: flex; align-items: center; gap: 5px; white-space: nowrap; }
  .contact-list strong { font-weight: 600; }
  .contact-icon { width: 8px; height: 8px; flex: none; stroke: var(--brand-blue); fill: none; stroke-width: 1.2; }
  .icon-spacer { width: 8px; flex: none; }
  .contact-list--phones { left: 26px; top: 694px; }
  .contact-list--web { left: 362px; top: 694px; }

  .closing-plain { position: absolute; left: 0; right: 0; top: 647px; text-align: center; font-size: 8.6px; }
  .rule-closing { left: 205px; width: 123px; top: 670px; }
  .ad-page--bleed .brand-mark { top: 682px; }
  .contact-row { position: absolute; left: 0; right: 0; top: 710px; display: flex; justify-content: center; gap: 11px; font-size: 8.4px; list-style: none; }
  .contact-row li { display: flex; align-items: center; gap: 4px; white-space: nowrap; }
</style>
</head>
<body>

<svg width="0" height="0" style="position:absolute" aria-hidden="true">
  <defs>
    <symbol id="icon-phone" viewBox="0 0 10 10"><path d="M2 1.2 L3.6 1 L4.3 3 L3.3 3.8 Q4.3 5.8 6.2 6.7 L7 5.7 L9 6.4 L8.8 8 Q5 8.6 1.8 5 Q1.3 3 2 1.2Z"/></symbol>
    <symbol id="icon-mail" viewBox="0 0 10 10"><rect x="1" y="2" width="8" height="6"/><path d="M1 2 L5 5.5 L9 2"/></symbol>
    <symbol id="icon-globe" viewBox="0 0 10 10"><circle cx="5" cy="5" r="4"/><ellipse cx="5" cy="5" rx="1.8" ry="4"/><path d="M1 5 H9"/></symbol>
  </defs>
</svg>

<!-- Variation A: framed hero -->
<article class="ad-page ad-page--framed">
  <div class="hero-photo" role="img" aria-label="Photograph of an explorer in a red hat standing at the bright mouth of a glowing blue glacier ice cave"></div>
  <h1 class="display headline-stack">ONCE-IN-A-LIFE TIME<br>EXPERIENCE</h1>

  <p class="invite">Imagine what we could do if we shared our ideas</p>
  <div class="rule-h rule-invite"></div>

  <div class="intro-copy">
    <p>For those who’ve explored the world and crave something beyond the ordinary.</p>
    <p>Each journey is a masterfully curated experience, rich in detail, seamless in execution, and unforgettable in every way.</p>
    <p>Founded in 1997, Tidewell Journeys is a unique travel company specializing in cruising, all-inclusive luxury properties, and tours world-wide for individuals, groups, and incentives.</p>
    <p>We offer an exceptional range of services designed to ensure every journey is flawlessly executed and truly unforgettable.</p>
  </div>
  <div class="rule-v rule-left"></div>
  <div class="gallery-photo gallery-photo--ship" role="img" aria-label="Photograph of a large cruise ship at sea under a cloudy sky"></div>
  <div class="gallery-photo gallery-photo--park" role="img" aria-label="Photograph of a colourful mosaic park overlooking a city at sunset"></div>
  <div class="rule-v rule-right"></div>

  <div class="benefits">
    <div class="benefit"><h3>ONE-OF-A-KIND LUXURY TRAVEL</h3><p>Once-in-a-lifetime experiences that are curated with creativity and meticulous attention to detail</p></div>
    <div class="benefit"><h3>EXCEPTIONAL SERVICE</h3><p>White-glove, personalized planning from start to finish</p></div>
    <div class="benefit"><h3>38 YEARS’ TRAVEL EXPERIENCE</h3><p>Expert knowledge of destinations, modes of travel, premium accommodations and well-established, meaningful industry connections.</p></div>
    <div class="benefit"><h3>HIGHLY TRUSTED</h3><p>Cruise line executives often say, <em>“No one does what you do.”</em></p></div>
  </div>

  <ul class="contact-list contact-list--phones">
    <li><svg class="contact-icon"><use href="#icon-phone"/></svg><span><strong>toll-free:</strong> 877.555.0142</span></li>
    <li><span class="icon-spacer"></span><span><strong>p:</strong> 816.555.0198</span></li>
  </ul>
  <div class="brand-mark"><span class="brand-dot"></span><span class="brand-name">Tidewell Journeys</span></div>
  <p class="closing-bold">Let us help you<br>plan your next extraordinary adventure.</p>
  <ul class="contact-list contact-list--web">
    <li><svg class="contact-icon"><use href="#icon-mail"/></svg>travelplans@tidewelljourneys-example.com</li>
    <li><svg class="contact-icon"><use href="#icon-globe"/></svg>tidewelljourneys-example.com</li>
  </ul>
</article>

<!-- Variation B: full-bleed hero -->
<article class="ad-page ad-page--bleed">
  <div class="hero-photo" role="img" aria-label="Photograph of an explorer in a red hat standing at the bright mouth of a glowing blue glacier ice cave"></div>
  <h1 class="display headline-centered">
    <span class="kicker">FOUR DECADES OF INSPIRATION</span>
    <span class="main">ONCE-IN-A-LIFE TIME EXPERIENCE</span>
    <span class="tail">COMES YOUR WAY</span>
  </h1>

  <p class="invite">Imagine what we could do if we shared our ideas</p>
  <div class="rule-h rule-invite"></div>

  <div class="intro-copy">
    <p>For those who’ve explored the world and crave something beyond the ordinary.</p>
    <p>Each journey is a masterfully curated experience, rich in detail, seamless in execution, and unforgettable in every way.</p>
    <p>Founded in 1997, Tidewell Journeys is a unique travel company specializing in cruising, all-inclusive luxury properties, and tours world-wide for individuals, groups, and incentives.</p>
    <p>We offer an exceptional range of services designed to ensure every journey is flawlessly executed and truly unforgettable.</p>
  </div>
  <div class="rule-v rule-left"></div>
  <div class="gallery-photo gallery-photo--ship" role="img" aria-label="Photograph of a large cruise ship at sea under a cloudy sky"></div>
  <div class="gallery-photo gallery-photo--park" role="img" aria-label="Photograph of a colourful mosaic park overlooking a city at sunset"></div>
  <div class="rule-v rule-right"></div>

  <div class="benefits">
    <div class="benefit"><h3>ONE-OF-A-KIND LUXURY TRAVEL</h3><p>Once-in-a-lifetime experiences that are curated with creativity and meticulous attention to detail</p></div>
    <div class="benefit"><h3>EXCEPTIONAL SERVICE</h3><p>White-glove, personalized planning from start to finish</p></div>
    <div class="benefit"><h3>38 YEARS’ TRAVEL EXPERIENCE</h3><p>Expert knowledge of destinations, modes of travel, premium accommodations and well-established, meaningful industry connections.</p></div>
    <div class="benefit"><h3>HIGHLY TRUSTED</h3><p>Cruise line executives often say, <em>“No one does what you do.”</em></p></div>
  </div>

  <p class="closing-plain">Let us help you plan your next extraordinary adventure.</p>
  <div class="rule-h rule-closing"></div>
  <div class="brand-mark"><span class="brand-dot"></span><span class="brand-name">Tidewell Journeys</span></div>
  <ul class="contact-row">
    <li>toll-free 877.555.0142</li>
    <li><svg class="contact-icon"><use href="#icon-phone"/></svg>816.555.0198</li>
    <li><svg class="contact-icon"><use href="#icon-mail"/></svg>travelplans@tidewelljourneys-example.com</li>
    <li><svg class="contact-icon"><use href="#icon-globe"/></svg>tidewelljourneys-example.com</li>
  </ul>
</article>

</body>
</html>
```